furniture and home contents restoration

I need to list the services that we perform in our studio.
we serve the general public as well as the insurance/ remediation industry

```html
<!DOCTYPE html>
<html lang="en">
<head>
<meta charset="utf-8">
<title>Kestrel Refinishers – Business Cards</title>
<link href="https://fonts.googleapis.com/css2?family=Lora:wght@400;700&display=swap" rel="stylesheet">
<style>
  :root {
    --stage: #e9e7e4;
    --card-top: #243c47;
    --card-bottom: #1b2f38;
    --ink: #f4f6f6;
    --ink-soft: #dfe6e8;
  }
  * { margin: 0; padding: 0; box-sizing: border-box; }
  html, body { width: 1200px; height: 930px; overflow: hidden; }
  body {
    background: var(--stage);
    font-family: "Lora", Georgia, serif;
    color: var(--ink);
    position: relative;
  }
  .card {
    position: absolute;
    width: 700px;
    height: 400px;
    border-radius: 18px;
    background: linear-gradient(160deg, var(--card-top), var(--card-bottom));
    box-shadow: 0 6px 18px rgba(0,0,0,.25);
    overflow: hidden;
  }
  .card--services { left: 80px; top: 45px; }
  .card--contact { left: 420px; top: 485px; }

  /* services side */
  .services__title {
    text-align: center;
    font-weight: 700;
    font-size: 34px;
    letter-spacing: 1px;
    margin-top: 34px;
  }
  .services__columns {
    display: flex;
    justify-content: space-between;
    gap: 20px;
    padding: 18px 34px 0 36px;
  }
  .services__list {
    list-style: none;
    font-size: 11.5px;
    line-height: 18px;
    text-transform: uppercase;
    letter-spacing: .2px;
    white-space: nowrap;
  }
  .services__list li::before { content: "• "; }
  .services__footer {
    position: absolute;
    left: 0; right: 0; bottom: 30px;
    text-align: center;
    font-size: 15px;
    line-height: 22px;
    text-transform: uppercase;
    letter-spacing: .4px;
  }

  /* contact side */
  .contact__tagline-top {
    position: absolute;
    right: 44px; top: 40px;
    font-size: 17px;
    text-transform: uppercase;
    letter-spacing: .5px;
    white-space: nowrap;
  }
  .contact__brand {
    position: absolute;
    left: 46px; top: 118px;
    font-weight: 700;
    font-size: 36px;
    line-height: 38px;
    letter-spacing: 1px;
  }
  .contact__name {
    position: absolute;
    left: 46px; bottom: 118px;
    font-weight: 700;
    font-size: 25px;
    letter-spacing: 1px;
    white-space: nowrap;
  }
  .contact__row {
    position: absolute;
    left: 46px; right: 36px; bottom: 40px;
    display: flex;
    align-items: flex-end;
    gap: 24px;
    white-space: nowrap;
  }
  .contact__divider {
    width: 2px;
    height: 62px;
    background: var(--ink);
    align-self: center;
  }
  .contact__lines { list-style: none; font-size: 16px; line-height: 22px; color: var(--ink-soft); }
  .contact__lines li { display: flex; align-items: flex-start; gap: 7px; }
  .contact__lines svg { width: 13px; height: 13px; margin-top: 5px; flex: none; fill: none; stroke: var(--ink); stroke-width: 1.6; }
  .contact__lines .indent { padding-left: 20px; }
  .contact__service { font-size: 16px; line-height: 22px; color: var(--ink-soft); text-align: center; align-self: flex-start; }
</style>
</head>
<body>

<section class="card card--services">
  <h1 class="services__title">KESTREL REFINISHERS</h1>
  <div class="services__columns">
    <ul class="services__list">
      <li>Antique repair and restoration</li>
      <li>Art cleaning and remounting</li>
      <li>Art and mirror frame repair</li>
      <li>Chandelier cleaning and restoration</li>
      <li>Document restoration</li>
      <li>Glass, ceramic, and mirror repair</li>
      <li>Hardware repair and restoration</li>
      <li>Kitchen removal and reinstallation</li>
      <li>Lamp cleaning and restoration</li>
      <li>Lamp shade replacement</li>
    </ul>
    <ul class="services__list">
      <li>Metal polishing and restoration</li>
      <li>Odor removal and ozone services</li>
      <li>Photo restoration</li>
      <li>Upholstery cleaning and deodorizing</li>
      <li>In-house upholstery and reupholstery</li>
      <li>Rug cleaning and restoration</li>
      <li>Musical instrument restoration</li>
      <li>Window treatment repair/ restoration</li>
      <li>Leather restoration and replacement</li>
      <li>Piano restoration and repair</li>
    </ul>
  </div>
  <p class="services__footer">On-site inspections and desk review services<br>Assessment reports and estimates for repair and restoration</p>
</section>

<section class="card card--contact">
  <p class="contact__tagline-top">Home contents restoration</p>
  <h2 class="contact__brand">KESTREL<br>REFINISHERS</h2>
  <p class="contact__name">DANIEL MORETTI</p>
  <div class="contact__row">
    <ul class="contact__lines">
      <li><svg viewBox="0 0 16 16"><path d="M4 1.5l2.5 3-1.5 2c1 2 2.5 3.5 4.5 4.5l2-1.5 3 2.5-1.5 2.5C7 14 2 9 1.5 3z"/></svg>914 555 0140</li>
      <li><svg viewBox="0 0 16 16"><rect x="4" y="1" width="8" height="14" rx="1.5"/><path d="M7 12.5h2"/></svg>914 555 0172</li>
      <li><svg viewBox="0 0 16 16"><rect x="2" y="6" width="12" height="8" rx="1"/><path d="M4 6V2h8v4M5 10h6"/></svg>914 555 0136</li>
    </ul>
    <span class="contact__divider"></span>
    <ul class="contact__lines">
      <li><svg viewBox="0 0 16 16"><path d="M8 15s-5-5.5-5-9a5 5 0 0110 0c0 3.5-5 9-5 9z"/><circle cx="8" cy="6" r="1.7"/></svg>212 elmwood ave.</li>
      <li class="indent">rivertown, ny 10599</li>
      <li><svg viewBox="0 0 16 16"><rect x="1.5" y="3.5" width="13" height="9" rx="1"/><path d="M1.5 4l6.5 5 6.5-5"/></svg>studio@kestrelco.com</li>
    </ul>
    <span class="contact__divider"></span>
    <p class="contact__service">serving the general public<br>and the insurance industry<br>for over 40 years</p>
  </div>
</section>

</body>
</html>
```